Business Card Design Project

I need a business card designed from scratch. I have an existing logo that I can upload in Illustrator for modification or redesign.

The Company is called Query Lanterns http://querylanterns.com.au and we provide Search Engine Optimization services to Australian businesses. The current logo signifies an increase in visitors, profits etc...

There are no restrictions as to the redesign - colours, style etc are all open to change.

Cards will be full colour and one sided printed at http://www.cardmoxel.com.au so check their requirements for file format and sizes etc.

I will expect all original files upon completion of project.

Target Market(s)

Any business with a web site looking to improve their search engine rankings

Industry/Entity Type

Business

Requirements
Must have
• I like modern, sleek designs. Clean, not fussy, uncluttered.

```html
<!DOCTYPE html>
<html lang="en">
<head>
<meta charset="utf-8">
<title>Query Lanterns – Business Cards</title>
<link rel="stylesheet" href="https://fonts.googleapis.com/css2?family=Source+Sans+3:wght@400;700&display=swap">
<style>
  :root {
    --backdrop: #d9dadc;
    --card-white: #ffffff;
    --card-black: #000000;
    --brand-blue: #1f6fb8;
    --deep-blue: #1a4f8a;
    --accent-yellow: #f6c31f;
    --warm-yellow: #f9b42a;
    --ink-grey: #444547;
    --text-light: #ffffff;
  }
  * { box-sizing: border-box; margin: 0; padding: 0; }
  html, body {
    width: 1200px; height: 965px; overflow: hidden;
    background: var(--backdrop);
    font-family: "Source Sans 3", "Myriad Pro", sans-serif;
  }
  .card {
    position: absolute;
    top: 62px;
    width: 486px; height: 853px;
    border-radius: 26px;
    overflow: hidden;
    background: var(--card-white);
    box-shadow: 0 4px 14px rgba(0,0,0,0.18);
  }
  .card--front { left: 48px; }
  .card--back { left: 658px; }
  .card__art {
    position: absolute; inset: 0;
    width: 100%; height: 100%;
  }
  .card__dark-field { fill: var(--card-black); }
  .grad-start { stop-color: var(--warm-yellow); }
  .grad-mid { stop-color: var(--accent-yellow); }
  .grad-end { stop-color: var(--brand-blue); }

  .brand {
    position: absolute; top: 74px; left: 34px;
    display: flex; align-items: center; gap: 14px;
  }
  .brand__dot {
    width: 22px; height: 22px; border-radius: 50%;
    background: var(--accent-yellow);
  }
  .brand__name {
    font-size: 46px; font-weight: 700; line-height: 1;
    color: var(--brand-blue);
  }

  .address {
    position: absolute; right: 42px; top: 758px;
    text-align: right;
    font-size: 20px; line-height: 30px;
    color: var(--text-light);
  }

  .person {
    position: absolute; top: 62px; left: 44px;
    color: var(--ink-grey);
  }
  .person__name { font-size: 35px; font-weight: 700; line-height: 1.1; }
  .person__role { font-size: 27px; font-weight: 400; line-height: 1.3; }

  .contacts {
    position: absolute; left: 50px; top: 678px;
    list-style: none;
    font-size: 20px; line-height: 28px;
    color: var(--text-light);
  }
  .contacts__label { font-weight: 700; }
</style>
</head>
<body>
  <section class="card card--front">
    <svg class="card__art" viewBox="0 0 486 853" preserveAspectRatio="none">
      <defs>
        <linearGradient id="rise-front" x1="0" y1="1" x2="1" y2="0">
          <stop class="grad-start" offset="0"/>
          <stop class="grad-mid" offset="0.35"/>
          <stop class="grad-end" offset="0.8"/>
        </linearGradient>
      </defs>
      <polygon class="card__dark-field" points="0,600 486,360 486,853 0,853"/>
      <polygon role="img" aria-label="Rising growth ribbon graphic in blue and yellow"
               fill="url(#rise-front)" points="0,420 486,70 486,400 0,740"/>
    </svg>
    <div class="brand">
      <span class="brand__dot"></span>
      <span class="brand__name">Query Lanterns</span>
    </div>
    <p class="address">25 Street Name, Road Name,<br>State, Country Code</p>
  </section>

  <section class="card card--back">
    <svg class="card__art" viewBox="0 0 486 853" preserveAspectRatio="none">
      <defs>
        <linearGradient id="rise-back" x1="0" y1="1" x2="1" y2="0">
          <stop class="grad-start" offset="0"/>
          <stop class="grad-mid" offset="0.35"/>
          <stop class="grad-end" offset="0.8"/>
        </linearGradient>
      </defs>
      <polygon class="card__dark-field" points="0,500 486,200 486,853 0,853"/>
      <polygon role="img" aria-label="Rising growth ribbon graphic in blue and yellow"
               fill="url(#rise-back)" points="0,300 486,0 486,330 0,620"/>
    </svg>
    <div class="person">
      <p class="person__name">Name</p>
      <p class="person__role">Administrator</p>
    </div>
    <ul class="contacts">
      <li><span class="contacts__label">Phone.</span> 001-123-123456</li>
      <li><span class="contacts__label">Fax.</span> 001-123-123456</li>
      <li><span class="contacts__label">Cell.</span> 001-123-123456</li>
      <li><span class="contacts__label">Email.</span> querylanterns@gmail.com</li>
      <li><span class="contacts__label">Web.</span> www.Website.com</li>
    </ul>
  </section>
</body>
</html>
```